I need a shopify website for a beauty brand that i am starting. The name of the brand is called "Morwen Beauty" i need the website to have a "Sleek Sexy And Mordern Design" preferable with a "Black Colour Scheme" i need the shopify store to be "Integrated With Instagram and Facebook" (@MorwenBeauty on Instagram and Morwen Beauty On Facebook) ... I Also need to be able to "Easily to upload future products" (as ive only got three products at the moment) and i will also need to be "Able to capture emails to use for email marketing in the future as the brand grows "

```html
<!DOCTYPE html>
<html lang="en">
<head>
<meta charset="utf-8">
<title>Morwen Beauty</title>
<link rel="stylesheet" href="https://fonts.googleapis.com/css2?family=Open+Sans:wght@400;600;700&family=Poppins:wght@600;700&display=swap">
<style>
:root{
  --ink:#111111;
  --white:#ffffff;
  --muted:#333333;
  --rule:#9a9a9a;
  --card:#f3f0f0;
  --footer:#222222;
  --hero-dark:#0d0d0d;
  --blush-light:#d9b3a6;
  --blush-dark:#a5807a;
}
*{box-sizing:border-box;margin:0;padding:0}
html,body{width:1200px;height:3431px;overflow:hidden;background:var(--white)}
body{font-family:"Open Sans",Arial,sans-serif;color:var(--ink);position:relative}
.abs{position:absolute}
.heading{font-family:"Poppins",Arial,sans-serif;font-weight:700}

/* header */
.site-header{position:absolute;top:0;left:0;width:1200px;height:108px;background:var(--white)}
.brand{left:132px;top:22px;width:150px;text-align:center;font-weight:700;font-size:19px;letter-spacing:2px;line-height:1.3;color:var(--ink)}
.nav{left:477px;top:43px;display:flex;gap:37px;font-size:14px;font-weight:600;list-style:none}
.nav li.active{text-decoration:underline;text-underline-offset:4px;font-weight:700}
.cart{left:1025px;top:34px}

/* hero */
.hero{top:108px;left:0;width:1200px;height:631px;background:linear-gradient(90deg,var(--hero-dark) 0%,#121212 35%,#1d1816 55%,#4a3a33 68%,#171412 85%,#0c0c0c 100%)}
.hero-kicker{left:132px;top:180px;color:var(--white);font-size:26px;letter-spacing:1px}
.hero-title{left:132px;top:215px;color:var(--white);font-size:44px;letter-spacing:2px}
.hero-copy{left:132px;top:290px;width:320px;color:var(--white);font-size:20px;line-height:31px}
.btn-outline{display:flex;align-items:center;justify-content:center;border:3px solid var(--white);color:var(--white);font-weight:600;text-transform:uppercase}
.hero-btn{left:133px;top:385px;width:141px;height:50px;font-size:18px}
.hero-arrows{left:1103px;top:565px}

/* categories */
.section-title{width:1200px;left:0;text-align:center;font-size:24px}
.cat-title{top:788px}
.title-rule{left:570px;top:834px;width:60px;height:2px;background:var(--rule)}
.lash-art{background:radial-gradient(ellipse at center,#3a3a3a 0%,#8a8a8a 45%,#ffffff 72%)}
.category{width:300px;text-align:center}
.category .lash-art{width:220px;height:170px;margin:0 auto}
.category h3{font-size:15px;font-weight:700;margin-top:34px}
.category p{font-size:15px;margin-top:6px}

/* latest lash */
.lash-banner{top:1188px;left:0;width:1200px;height:525px;background:linear-gradient(90deg,#c4a092 0%,#d6b2a6 35%,var(--blush-light) 55%,var(--blush-dark) 100%)}
.banner-title{left:702px;top:1328px;color:var(--white);font-size:45px}
.banner-copy{left:705px;top:1398px;width:340px;color:var(--white);font-size:19px;line-height:28px}
.banner-btn{left:707px;top:1482px;width:141px;height:52px;font-size:18px}

/* products */
.products-title{top:1768px}
.product{top:1838px;width:228px;height:267px;background:var(--card);text-align:center}
.product .lash-art{width:190px;height:110px;margin:60px auto 0;background:radial-gradient(ellipse at center,#2d2d2d 0%,#8c8c8c 40%,var(--card) 70%)}
.product .name{font-size:14px;margin-top:30px}
.product .price{font-size:14px;font-weight:700;margin-top:10px}

/* trending */
.trending-title{top:2175px}
.collection{top:2254px;width:300px;text-align:center}
.collection .photo{height:234px}
.collection .label{font-size:14px;font-weight:700;margin-top:20px}

/* feature split */
.feature-photo{left:0;top:2609px;width:690px;height:509px;background:linear-gradient(180deg,#7a5a48 0%,#c59a80 40%,#d9ae93 70%,#a84a4a 100%)}
.feature-title{left:746px;top:2700px;width:400px;font-size:25px;line-height:35px;text-transform:uppercase}
.feature-copy{left:746px;top:2832px;width:330px;font-size:14px;line-height:20px;color:var(--muted)}
.btn-solid{left:748px;top:2966px;width:112px;height:36px;background:var(--ink);color:var(--white);font-size:14px;font-weight:600;display:flex;align-items:center;justify-content:center}

/* footer */
.site-footer{left:0;top:3118px;width:1200px;height:313px;background:var(--footer);color:var(--white)}
.foot-head{font-size:16px;font-weight:700;top:52px}
.foot-about{left:132px;top:94px;width:285px;font-size:13px;line-height:21px}
.foot-menu{left:498px;top:78px;list-style:none;font-size:13px;line-height:21px}
.foot-join{left:724px;top:80px;font-size:13px}
.subscribe{left:725px;top:120px;width:340px;height:46px;border:2px solid var(--white);display:flex}
.subscribe span{flex:1;font-size:11px;padding:14px 16px;color:#dddddd}
.subscribe .go{width:46px;background:var(--white);display:flex;align-items:center;justify-content:center}
.social{left:134px;top:248px;display:flex;gap:8px}
.social span{width:27px;height:27px;border-radius:50%}
.copyright{left:0;width:1200px;top:255px;text-align:center;font-size:11px}
.payments{left:863px;top:248px;display:flex;gap:9px}
.payments span{width:44px;height:29px;border-radius:3px}
</style>
</head>
<body>

<header class="site-header">
  <div class="abs brand">MORWEN<br>BEAUTY</div>
  <ul class="abs nav">
    <li class="active">HOME</li><li>ABOUT</li><li>PRODUCTS</li><li>SERVICES</li><li>BLOG</li><li>CONTACT</li>
  </ul>
  <svg class="abs cart" width="44" height="40" viewBox="0 0 44 40" aria-label="Cart">
    <path d="M2 8h6l5 18h18l4-13H10" fill="none" stroke="#111" stroke-width="2.4" stroke-linejoin="round"/>
    <path d="M14 17h19M15 21h17M18 13v13M23 13v13M28 13v13" stroke="#111" stroke-width="1.5"/>
    <circle cx="16" cy="32" r="2.6" fill="#111"/><circle cx="29" cy="32" r="2.6" fill="#111"/>
    <circle cx="34" cy="10" r="8" fill="#111"/>
    <text x="34" y="14" fill="#fff" font-family="Open Sans,sans-serif" font-size="11" font-weight="700" text-anchor="middle">0</text>
  </svg>
</header>

<section class="abs hero" role="img" aria-label="Portrait photograph of a woman wearing full lashes against a black background">
  <div class="abs hero-kicker heading">WELCOME TO</div>
  <h1 class="abs hero-title heading">MORWEN BEAUTY</h1>
  <p class="abs hero-copy">Lorem Ipsum is simply dummy text of the printing</p>
  <div class="abs btn-outline hero-btn">Shop now</div>
  <svg class="abs hero-arrows" width="50" height="26" viewBox="0 0 50 26" aria-label="Slide controls">
    <path d="M14 3 5 13l9 10M36 3l9 10-9 10" fill="none" stroke="#fff" stroke-width="2.6"/>
  </svg>
</section>

<h2 class="abs section-title heading cat-title">CATEGORIES</h2>
<div class="abs title-rule"></div>
<div class="abs category" style="left:100px;top:879px">
  <div class="lash-art" role="img" aria-label="Pair of wispy false lashes"></div>
  <h3>LOREM IPSUM IS SIMPLY</h3><p>There are many variations</p>
</div>
<div class="abs category" style="left:459px;top:879px">
  <div class="lash-art" role="img" aria-label="Pair of dense false lashes"></div>
  <h3>GET WELL</h3><p>There are many variations</p>
</div>
<div class="abs category" style="left:799px;top:879px">
  <div class="lash-art" role="img" aria-label="Pair of long volume false lashes"></div>
  <h3>LOVE &amp; ROMANCE</h3><p>There are many variations</p>
</div>

<section class="abs lash-banner" role="img" aria-label="Close-up photograph of an eye wearing long lashes"></section>
<h2 class="abs banner-title heading">Latest Lash</h2>
<p class="abs banner-copy">There are many variations of passages of Lorem Ipsum available</p>
<div class="abs btn-outline banner-btn">Shop now</div>

<h2 class="abs section-title heading products-title">OUR PRODUCTS</h2>
<div class="abs product" style="left:130px"><div class="lash-art" role="img" aria-label="False lash product"></div><p class="name">LOREM IPSUM IS SIMPLY</p><p class="price">$15.99</p></div>
<div class="abs product" style="left:369px"><div class="lash-art" role="img" aria-label="False lash product"></div><p class="name">LOREM IPSUM IS SIMPLY</p><p class="price">$15.99</p></div>
<div class="abs product" style="left:607px"><div class="lash-art" role="img" aria-label="False lash product"></div><p class="name">LOREM IPSUM IS SIMPLY</p><p class="price">$15.99</p></div>
<div class="abs product" style="left:843px"><div class="lash-art" role="img" aria-label="False lash product"></div><p class="name">LOREM IPSUM IS SIMPLY</p><p class="price">$15.99</p></div>

<h2 class="abs section-title heading trending-title">TRENDING COLLECTIONS</h2>
<div class="abs collection" style="left:133px"><div class="photo" role="img" aria-label="Close-up of closed eyes with pink shadow" style="background:linear-gradient(180deg,#b88e80,#e0b5aa,#d9ab98)"></div><p class="label">LOREM IPSUM</p></div>
<div class="abs collection" style="left:453px"><div class="photo" role="img" aria-label="Model looking up with smoky eye makeup" style="background:linear-gradient(90deg,#9a9aae,#b9b7c6 40%,#e4c3b3)"></div><p class="label">LOREM IPSUM</p></div>
<div class="abs collection" style="left:770px"><div class="photo" role="img" aria-label="Close-up of green eyes with natural lashes" style="background:linear-gradient(180deg,#c99a72,#f1d3b6,#e9c5a4)"></div><p class="label">LOREM IPSUM</p></div>

<section class="abs feature-photo" role="img" aria-label="Close-up of a face with closed eyes, long lashes and red lips"></section>
<h2 class="abs feature-title heading">Lorem Ipsum is simply dummy text of the printing and typesetting industry</h2>
<p class="abs feature-copy">Sed ut perspiciatis unde omnis iste natus error sit voluptatem accusantium doloremque laudantium, totam rem aperiam, eaque ipsa quae ab illo inventore veritatis et quasi architecto beatae vitae dicta sunt explicabo.</p>
<div class="abs btn-solid">SHOP NOW</div>

<footer class="abs site-footer">
  <h4 class="abs foot-head heading" style="left:133px;font-size:16px">ABOUT</h4>
  <p class="abs foot-about">Lorem Ipsum is simply dummy text of the printing and typesetting industry.  veritatis et qai architecto beatae vitae dicta sunt explicabo. Nemo enim ipsam</p>
  <h4 class="abs foot-head heading" style="left:498px">MENU</h4>
  <ul class="abs foot-menu"><li>Home</li><li>About</li><li>Products</li><li>Services</li><li>Blog</li><li>Contact</li></ul>
  <h4 class="abs foot-head heading" style="left:724px">STAY CONNECTED</h4>
  <p class="abs foot-join">Join our mailing list to get updates</p>
  <div class="abs subscribe"><span>E mail address</span><div class="go"><svg width="14" height="18" viewBox="0 0 14 18"><path d="M3 2l7 7-7 7" fill="none" stroke="#111" stroke-width="2"/></svg></div></div>
  <div class="abs social" aria-label="Social links">
    <span style="background:#3b5aa5"></span><span style="background:#2aa3ef"></span><span style="background:#8a8aa6"></span>
  </div>
  <p class="abs copyright">Copyright © 2021 All Rights Reserved</p>
  <div class="abs payments" aria-label="Accepted payment methods">
    <span style="background:#1d3c8f"></span><span style="background:#1a4fb0"></span><span style="background:#3a3a3a"></span><span style="background:#2779cf"></span>
  </div>
</footer>

</body>
</html>
```